Residential Remodeling Contractor needs updated business card

I need a new design for my business card.
Name of the company is Ridgefell Construction. I need a card that commands presence, strength, integrity. I have been in business for 28 years. I am a Residential Remodeling Contractor that covers all aspects of a residential remodel and build.

```html
<!DOCTYPE html>
<html lang="en">
<head>
<meta charset="utf-8">
<title>Ridgefell Construction – Business Card</title>
<link rel="stylesheet" href="https://fonts.googleapis.com/css2?family=Montserrat:wght@400;600;700&display=swap">
<style>
  :root {
    --backdrop: #8e8e8e;
    --navy: #1f3d7e;
    --navy-deep: #19336b;
    --paper: #fbfbfb;
    --ink-dark: #333333;
    --ink-soft: #6b6b6b;
  }
  * { margin: 0; padding: 0; box-sizing: border-box; }
  html, body {
    width: 1200px;
    height: 1200px;
    overflow: hidden;
    background: var(--backdrop);
    font-family: "Montserrat", sans-serif;
  }
  .card {
    position: absolute;
    left: 226px;
    width: 746px;
    height: 436px;
    border-radius: 25px;
  }
  .card-front {
    top: 130px;
    background: var(--navy);
    display: flex;
    flex-direction: column;
    align-items: center;
    justify-content: center;
  }
  .front-wordmark {
    color: var(--navy-deep);
    font-weight: 700;
    text-transform: uppercase;
    text-align: center;
    line-height: 1.05;
    margin-top: -28px;
  }
  .front-wordmark .line-one { display: block; font-size: 66px; letter-spacing: 2px; }
  .front-wordmark .line-two { display: block; font-size: 48px; letter-spacing: 1px; }
  .card-back {
    top: 639px;
    background: var(--paper);
  }
  .back-wordmark {
    position: absolute;
    left: 80px;
    top: 178px;
    color: var(--navy);
    font-weight: 700;
    text-transform: uppercase;
    line-height: 1.1;
  }
  .back-wordmark .line-one { display: block; font-size: 33px; letter-spacing: 1px; }
  .back-wordmark .line-two { display: block; font-size: 24px; letter-spacing: 0.5px; }
  .contact-block {
    position: absolute;
    left: 404px;
    top: 150px;
  }
  .person-name {
    font-size: 17px;
    font-weight: 700;
    letter-spacing: 4px;
    color: var(--ink-dark);
    text-transform: uppercase;
  }
  .person-role {
    font-size: 18px;
    letter-spacing: 2.5px;
    color: var(--ink-soft);
    margin-top: 4px;
  }
  .contact-list {
    list-style: none;
    margin-top: 36px;
  }
  .contact-list li {
    display: flex;
    align-items: center;
    font-size: 19px;
    color: var(--ink-soft);
    letter-spacing: 0.3px;
    height: 29px;
  }
  .contact-list svg {
    width: 18px;
    height: 18px;
    margin-right: 15px;
    fill: var(--navy);
    flex-shrink: 0;
  }
</style>
</head>
<body>
  <section class="card card-front" aria-label="Card front">
    <div class="front-wordmark">
      <span class="line-one">Ridgefell</span>
      <span class="line-two">Construction</span>
    </div>
  </section>

  <section class="card card-back" aria-label="Card back">
    <div class="back-wordmark">
      <span class="line-one">Ridgefell</span>
      <span class="line-two">Construction</span>
    </div>

    <div class="contact-block">
      <p class="person-name">Name Surname</p>
      <p class="person-role">Position</p>
      <ul class="contact-list">
        <li>
          <svg viewBox="0 0 18 18" aria-hidden="true"><path d="M5 1h8a1.5 1.5 0 0 1 1.5 1.5v13A1.5 1.5 0 0 1 13 17H5a1.5 1.5 0 0 1-1.5-1.5v-13A1.5 1.5 0 0 1 5 1zm0.3 2v11h7.4V3zM9 14.6a.9.9 0 1 0 0 1.8.9.9 0 0 0 0-1.8z"/></svg>
          123-456-7890
        </li>
        <li>
          <svg viewBox="0 0 18 18" aria-hidden="true"><path d="M1 4h16v10H1zM2.2 5.2 9 10l6.8-4.8v-.1H2.2z"/></svg>
          email@website.com
        </li>
        <li>
          <svg viewBox="0 0 18 18" aria-hidden="true"><path d="M9 1.5a7.5 7.5 0 1 0 0 15 7.5 7.5 0 0 0 0-15zm0 1.3c.9 0 1.9 1.6 2.2 4.1H6.8C7.1 4.4 8.1 2.8 9 2.8zm-2.3.5A9 9 0 0 0 5.5 6.9H3.3a6.2 6.2 0 0 1 3.4-3.6zm4.6 0a6.2 6.2 0 0 1 3.4 3.6h-2.2a9 9 0 0 0-1.2-3.6zM3 8.1h2.4a13 13 0 0 0 0 1.8H3a6 6 0 0 1 0-1.8zm3.6 0h4.8a12 12 0 0 1 0 1.8H6.6a12 12 0 0 1 0-1.8zm6 0H15a6 6 0 0 1 0 1.8h-2.4a13 13 0 0 0 0-1.8zM3.3 11.1h2.2a9 9 0 0 0 1.2 3.6 6.2 6.2 0 0 1-3.4-3.6zm3.5 0h4.4c-.3 2.5-1.3 4.1-2.2 4.1s-1.9-1.6-2.2-4.1zm5.7 0h2.2a6.2 6.2 0 0 1-3.4 3.6 9 9 0 0 0 1.2-3.6z"/></svg>
          www.website.com
        </li>
      </ul>
    </div>
  </section>
</body>
</html>
```